Automotive eCommerce Business looking for a business card design

Looking for a clean and simple business card design. Our company name is "Brindle Auto" and we are a company specializing in the ecommerce sales of automotive parts, specifically for pick up trucks and large SUVs. Our company colours are red, black, and white.

Feel free to use the logo provided or create a new logo that you seem fit. Looking forward to your creative ideas!

Industry/Entity Type

Automotive

Contact Information for Business Card

We were thinking of a possibly two-sided design featuring just the logo and company name on one side, and personal information on the other side. Single sided designs will be considered as well.

Font styles to use
Serif
Sans Serif
Decorative

Colors
ec1f27
ffffff
000000

Requirements
Must have
• Space for employee's name, title, phone number and email address, along with the company address and website somewhere.

```html
<!DOCTYPE html>
<html lang="en">
<head>
<meta charset="utf-8">
<title>Brindle Auto Ltd. – Business Card</title>
<link rel="stylesheet" href="https://fonts.googleapis.com/css2?family=Cinzel:wght@600&family=Roboto:wght@400;500&family=Roboto+Condensed:wght@700&display=swap">
<style>
  :root {
    --brand-red: #ec1f27;
    --card-black: #222223;
    --backdrop: #2e2e30;
    --text-white: #ffffff;
    --text-soft: #e6e6e6;
    --divider: #9a9a9a;
  }
  * { box-sizing: border-box; margin: 0; padding: 0; }
  html, body { width: 1200px; height: 900px; overflow: hidden; }
  body {
    background: var(--backdrop);
    display: flex;
    flex-direction: column;
    align-items: center;
    justify-content: center;
    gap: 40px;
  }
  .card {
    width: 680px;
    height: 390px;
    background: var(--card-black);
    position: relative;
    box-shadow: 0 10px 30px rgba(0,0,0,.45);
  }

  /* Front side */
  .card-front {
    display: flex;
    flex-direction: column;
    align-items: center;
    justify-content: center;
  }
  .brand-mark {
    width: 96px;
    height: 96px;
    background: var(--brand-red);
    margin-bottom: 34px;
  }
  .brand-name {
    font-family: "Cinzel", serif;
    font-weight: 600;
    font-size: 32px;
    color: var(--text-white);
    letter-spacing: 1px;
  }
  .brand-web {
    margin-top: 22px;
    font-family: "Roboto", sans-serif;
    font-size: 15px;
    color: var(--text-soft);
    letter-spacing: 7px;
  }

  /* Back side */
  .card-back { padding: 0 60px; }
  .identity {
    position: absolute;
    right: 372px;
    top: 120px;
    text-align: right;
  }
  .person-name {
    font-family: "Roboto Condensed", sans-serif;
    font-weight: 700;
    font-size: 40px;
    line-height: 1;
    color: var(--brand-red);
    text-transform: uppercase;
  }
  .person-title {
    margin-top: 8px;
    font-family: "Roboto", sans-serif;
    font-weight: 500;
    font-size: 17px;
    color: var(--text-white);
    text-transform: uppercase;
  }
  .divider {
    position: absolute;
    left: 330px;
    top: 100px;
    width: 2px;
    height: 118px;
    background: linear-gradient(var(--divider), rgba(154,154,154,.2));
  }
  .contact-list {
    position: absolute;
    left: 358px;
    top: 100px;
    list-style: none;
  }
  .contact-item {
    display: flex;
    align-items: center;
    gap: 10px;
    font-family: "Roboto", sans-serif;
    font-weight: 500;
    font-size: 16px;
    line-height: 24px;
    color: var(--text-white);
  }
  .contact-icon { width: 15px; height: 15px; fill: var(--brand-red); flex: none; }
  .address {
    position: absolute;
    left: 160px;
    bottom: 70px;
    display: flex;
    align-items: center;
    gap: 6px;
    font-family: "Roboto", sans-serif;
    font-weight: 500;
    font-size: 18px;
    color: var(--text-white);
  }
  .address .contact-icon { width: 16px; height: 18px; }
</style>
</head>
<body>

  <section class="card card-front">
    <div class="brand-mark"></div>
    <h1 class="brand-name">Brindle Auto Ltd.</h1>
    <p class="brand-web">www.brindleauto.com</p>
  </section>

  <section class="card card-back">
    <div class="identity">
      <h2 class="person-name">Owen Hale</h2>
      <p class="person-title">CEO/Founder</p>
    </div>
    <div class="divider"></div>
    <ul class="contact-list">
      <li class="contact-item">
        <svg class="contact-icon" viewBox="0 0 16 16"><path d="M3.5 1l3 3-1.8 1.8a9 9 0 0 0 5.5 5.5L12 9.5l3 3-2 2.5C7 15 1 9 1 3z"/></svg>
        555 214 7730
      </li>
      <li class="contact-item">
        <svg class="contact-icon" viewBox="0 0 16 16"><path d="M4 0h8a1 1 0 0 1 1 1v14a1 1 0 0 1-1 1H4a1 1 0 0 1-1-1V1a1 1 0 0 1 1-1zm1 2v10h6V2zm3 11a1 1 0 1 0 0 2 1 1 0 0 0 0-2z"/></svg>
        555 390 1186
      </li>
      <li class="contact-item">
        <svg class="contact-icon" viewBox="0 0 16 16"><path d="M4 1h8v4H4zM1 6h14v7h-3v2H4v-2H1zm4 5v3h6v-3z"/></svg>
        555 672 4051
      </li>
      <li class="contact-item">
        <svg class="contact-icon" viewBox="0 0 16 16"><path d="M1 3h14v1.5L8 9 1 4.5zm0 3.3L8 11l7-4.7V13H1z"/></svg>
        owen@brindleauto.com
      </li>
      <li class="contact-item">
        <svg class="contact-icon" viewBox="0 0 16 16"><path d="M8 0a8 8 0 1 0 0 16A8 8 0 0 0 8 0zm0 2a6 6 0 0 1 5.7 4H2.3A6 6 0 0 1 8 2zm-5.7 8h11.4A6 6 0 0 1 2.3 10z"/></svg>
        shop.brindleauto.com
      </li>
    </ul>
    <p class="address">
      <svg class="contact-icon" viewBox="0 0 14 18"><path d="M7 0a7 7 0 0 0-7 7c0 5 7 11 7 11s7-6 7-11a7 7 0 0 0-7-7zm0 4a3 3 0 1 1 0 6 3 3 0 0 1 0-6z"/></svg>
      2140 Cedar Ridge Road, Fairbanks, Alaska 99701
    </p>
  </section>

</body>
</html>
```